BOLD & MINIMALIST DESIGN NEEDED

We want a very bold but minimalistic business card design that is impactful and utilizes both sides of the business card. Our current logo is included for your use.

We want bold fonts and good use of negative space. We don't want the logo to overpower the design.

Target Market(s)

Professionals who are building new commercial buildings.

Industry/Entity Type

Construction

Contact Information for Business Card

Name, Title, email, office phone, cell phone, website

Font styles to use
Serif
Sans Serif

Requirements
Must have
• Bold design!

```html
<!DOCTYPE html>
<html lang="en">
<head>
<meta charset="utf-8">
<title>Ridgeway Design + Build — Business Card</title>
<link rel="stylesheet" href="https://fonts.googleapis.com/css2?family=Montserrat:wght@400;700;800&display=swap">
<style>
  :root {
    --backdrop: #dcdcdc;
    --ink: #0d0e10;
    --paper: #ffffff;
    --accent: #7dc242;
    --muted: #7a7a7a;
  }
  * { margin: 0; padding: 0; box-sizing: border-box; }
  html, body { width: 1200px; height: 1200px; overflow: hidden; }
  body {
    background: var(--backdrop);
    font-family: "Montserrat", sans-serif;
    position: relative;
  }
  .card {
    position: absolute;
    left: 179px;
    width: 861px;
    height: 496px;
  }
  .card--front { top: 84px; background: var(--ink); }
  .card--back { top: 621px; background: var(--paper); }

  .front-brand {
    position: absolute;
    left: 0; right: 0; top: 0; bottom: 0;
    display: flex;
    align-items: center;
    justify-content: center;
    gap: 18px;
  }
  .brand-square {
    width: 34px; height: 34px;
    background: var(--accent);
  }
  .front-brand .brand-name {
    color: var(--paper);
    font-weight: 800;
    font-size: 40px;
    letter-spacing: 1px;
    text-transform: uppercase;
  }

  .back-brand {
    position: absolute;
    left: 57px;
    top: 205px;
    width: 353px;
    text-align: center;
    color: var(--ink);
    font-weight: 800;
    font-size: 29px;
    line-height: 1.2;
    text-transform: uppercase;
    letter-spacing: 0.5px;
  }

  .divider {
    position: absolute;
    left: 435px;
    top: 142px;
    width: 2px;
    height: 207px;
    background: var(--ink);
  }

  .contact {
    position: absolute;
    left: 454px;
    top: 133px;
  }
  .contact__name {
    font-weight: 700;
    font-size: 36px;
    color: var(--ink);
    line-height: 1.05;
    letter-spacing: 0.3px;
  }
  .contact__title {
    font-weight: 400;
    font-size: 31px;
    color: var(--accent);
    line-height: 1.15;
    letter-spacing: 1px;
    margin-bottom: 8px;
  }
  .contact__list { list-style: none; }
  .contact__row {
    display: flex;
    align-items: center;
    height: 35px;
    font-size: 24px;
    color: var(--muted);
    letter-spacing: 1.2px;
  }
  .contact__icon {
    width: 26px; height: 26px;
    margin-right: 15px;
    flex: none;
  }
  .highlight { color: var(--accent); }

  .back-square {
    position: absolute;
    left: 419px;
    top: 436px;
    width: 24px; height: 24px;
    background: var(--accent);
  }
  .base-band {
    position: absolute;
    left: 0; right: 0; bottom: 0;
    height: 7px;
    background: var(--ink);
  }
</style>
</head>
<body>
  <section class="card card--front">
    <div class="front-brand">
      <span class="brand-square"></span>
      <span class="brand-name">Ridgeway Design + Build</span>
    </div>
  </section>

  <section class="card card--back">
    <div class="back-brand">Ridgeway<br>Design + Build</div>
    <div class="divider"></div>

    <div class="contact">
      <p class="contact__name">Name Surename</p>
      <p class="contact__title">Director</p>
      <ul class="contact__list">
        <li class="contact__row">
          <svg class="contact__icon" viewBox="0 0 24 24" aria-hidden="true"><path fill="#0d0e10" d="M6.6 10.8a15 15 0 0 0 6.6 6.6l2.2-2.2c.3-.3.7-.4 1-.2 1.1.4 2.3.6 3.6.6.6 0 1 .4 1 1V20c0 .6-.4 1-1 1A17 17 0 0 1 3 4c0-.6.4-1 1-1h3.5c.6 0 1 .4 1 1 0 1.3.2 2.5.6 3.6.1.3 0 .7-.2 1z"/></svg>
          <span>555-014-2290</span>
        </li>
        <li class="contact__row">
          <svg class="contact__icon" viewBox="0 0 24 24" aria-hidden="true"><path fill="#0d0e10" d="M2 8c0-2 4-4 10-4s10 2 10 4v2h-5V8H7v2H2zM6 12l2-3h8l2 3v8H6z"/></svg>
          <span>555-014-2290</span>
        </li>
        <li class="contact__row">
          <svg class="contact__icon" viewBox="0 0 24 24" aria-hidden="true"><rect x="2" y="5" width="20" height="14" fill="none" stroke="#0d0e10" stroke-width="2"/><path d="M2 5l10 8 10-8M2 19l8-7M22 19l-8-7" fill="none" stroke="#0d0e10" stroke-width="1.6"/></svg>
          <span>info@r-d-b.com</span>
        </li>
        <li class="contact__row">
          <svg class="contact__icon" viewBox="0 0 24 24" aria-hidden="true"><g fill="none" stroke="#0d0e10" stroke-width="1.6"><circle cx="12" cy="12" r="10"/><ellipse cx="12" cy="12" rx="4.5" ry="10"/><path d="M2 12h20M4 7h16M4 17h16"/></g></svg>
          <span>www.<span class="highlight">r-d-b</span>.com</span>
        </li>
      </ul>
    </div>

    <span class="back-square"></span>
    <div class="base-band"></div>
  </section>
</body>
</html>
```